Companybrochure for Consulting & Financing Firm

I need to have a Company Brochure asap for our company. We have a website that describes what we do, but we need also a brochure, that can be sent by PDF of eventually be printed as well.

The brochure should be short but nice and appealing to the customers.

We provide professional management consulting and help our customers to get finance for very diferent projects. Our business has a lot to do with personal relations, but also we are very professional in the way we work and how develop the solutions for our clients. Our clients are mainly government-owned firm, but also private trading companies and wealthy private investors.

Our customers are mainly in Latin America, but the company is headquater is in Switzerland. We are opening offices in Panama and Caracas, this should be easaly be adabtable later.

Please have a look at our website www.vorelpartners.ch. In the brochure, we would segment our services in 1.) Project Developments 2.) Management Conulting 3.) Investment Management and 4.) Finance Solutions.

Also do have a look at www.vorelpartners.ch
(Click E for the English version)
Updates

I managed to put the Mock-Up to the Website.
It is actually not really a mock-up, it is a version I have designed myself.
Well as I am not a designer, I hope you can make it much better.
The content however is what I would put in any other design as well.

Target Market(s)

Top Management, Investors, Entrepreneurs, Government Officials

Industry/Entity Type

Management Consulting

Requirements
Must have
• Design should reflect this image elements:

We are entrepreneurs.
We are comitted to get things done.
We work closely with the client side by side.
We are a professional partner.
We are not afraid of delivering unconventional solutions.
We look at the problem from various angles.
We analyse, develop solutions and implent results.
Should not have
• Typical US-American style elements. We do not want to give the impression of being a US company.

We do not want to appear to be neo-liberal. We are a politically neutral professional consulting firm.

```html
<!DOCTYPE html>
<html lang="en">
<head>
<meta charset="utf-8">
<title>Company Brochure – Spread 5–6</title>
<link href="https://fonts.googleapis.com/css2?family=Open+Sans:wght@400;600;700&display=swap" rel="stylesheet">
<style>
  :root {
    --backdrop: #e6e8ec;
    --paper: #ffffff;
    --paper-shade: #e9ecf1;
    --blue-deep: #1f4f86;
    --blue-mid: #2f74b3;
    --blue-light: #5aa2d6;
    --header-dark: #3b5f8c;
    --header-light: #7d97b8;
    --rule: #27558f;
    --text-light: #eaf3fb;
  }
  * { box-sizing: border-box; margin: 0; padding: 0; }
  html, body {
    width: 1200px; height: 900px; overflow: hidden;
    background: var(--backdrop);
    font-family: "Open Sans", Arial, sans-serif;
  }
  .spread {
    position: absolute; left: 30px; top: 248px;
    width: 1140px; height: 404px;
    display: flex;
    box-shadow: 0 14px 34px rgba(0,0,0,.22);
  }
  .page {
    position: relative; width: 570px; height: 404px; overflow: hidden;
    background: linear-gradient(180deg, var(--paper) 0%, var(--paper-shade) 100%);
  }
  .page--left { background: linear-gradient(90deg, var(--paper-shade) 0%, var(--paper) 60%, #dfe3ea 100%); }
  .page--right { background: linear-gradient(90deg, #dde1e8 0%, var(--paper) 14%, var(--paper-shade) 100%); }

  .photo { position: absolute; }
  .photo--maze {
    left: 28px; top: 18px; width: 360px; height: 228px;
    background: radial-gradient(ellipse at 70% 35%, #d6e3f2 0%, #eef2f7 55%, #f5f6f8 100%);
  }
  .photo--team {
    left: 34px; top: 16px; width: 380px; height: 204px; border-radius: 14px;
    background: linear-gradient(100deg, #e4ddd6 0%, #d9d3cd 35%, #b7b8bd 70%, #6f7480 100%);
  }

  .panel {
    position: absolute; border-radius: 10px; overflow: hidden;
    background: linear-gradient(180deg, var(--blue-mid) 0%, var(--blue-light) 100%);
    color: var(--text-light);
    box-shadow: 0 3px 8px rgba(0,0,0,.18);
  }
  .panel__title {
    background: linear-gradient(180deg, var(--header-light) 0%, var(--header-dark) 100%);
    color: #fff; font-weight: 700; font-size: 17px;
    padding: 6px 14px; border-radius: 10px 10px 0 0;
  }
  .panel--finance { left: 232px; top: 140px; width: 318px; height: 168px; }
  .panel--finance .panel__body { padding: 10px 14px; font-size: 7.6px; line-height: 1.45; }
  .panel--finance p + p { margin-top: 6px; }

  .panel--approach { left: 250px; top: 166px; width: 304px; height: 110px; }
  .panel--approach .panel__title { font-size: 15px; }
  .approach-list { list-style: none; padding: 6px 12px; font-size: 8.4px; line-height: 1.38; }
  .approach-list li::before { content: "> "; }
  .approach-list li:nth-child(2) { padding-left: 4px; }
  .approach-list li:nth-child(3) { padding-left: 8px; }
  .approach-list li:nth-child(4) { padding-left: 12px; }
  .approach-list li:nth-child(5) { padding-left: 16px; }
  .approach-list li:nth-child(6) { padding-left: 20px; }
  .approach-list li:nth-child(7) { padding-left: 24px; }

  .footer-rule { position: absolute; left: 0; bottom: 14px; width: 570px; height: 24px; }
  .page-number {
    position: absolute; bottom: 14px; width: 22px; height: 22px;
    background: var(--blue-deep); color: #fff; font-weight: 700; font-size: 13px;
    display: flex; align-items: center; justify-content: center;
  }
  .page--left .page-number { left: 12px; }
  .page--right .page-number { right: 12px; }
</style>
</head>
<body>
  <main class="spread">
    <section class="page page--left">
      <div class="photo photo--maze" role="img" aria-label="Photo of a hand drawing a red path through a maze on a glass screen"></div>
      <div class="panel panel--finance">
        <h2 class="panel__title">&gt;&gt; Finance Solutions</h2>
        <div class="panel__body">
          <p>Financing growth opportunities sometimes calls for an entrepreneurial perspective, which is often not found in the traditional banking world.</p>
          <p>That is why we have committed ourselves to developing financing solutions for unconventional requirements. To do so, we often work with partners with complementary subject matter expertise and geographical coverage.</p>
          <p>This gives us the flexibility to create innovative solutions – solutions that meet our clients' special needs.</p>
        </div>
      </div>
      <svg class="footer-rule" viewBox="0 0 570 24" aria-hidden="true">
        <path d="M34 20 Q300 14 570 2" fill="none" stroke="var(--rule)" stroke-width="2"/>
      </svg>
      <div class="page-number">5</div>
    </section>

    <section class="page page--right">
      <div class="photo photo--team" role="img" aria-label="Photo of a smiling business team standing in a row with arms crossed"></div>
      <div class="panel panel--approach">
        <h2 class="panel__title">&gt; Analyze &gt;&gt; Develop &gt;&gt;&gt; Deliver</h2>
      </div>
      <ul class="approach-list" style="position:absolute;left:250px;top:196px;width:304px;color:var(--text-light);background:linear-gradient(180deg,var(--blue-mid),var(--blue-light));border-radius:0 0 10px 10px;box-shadow:0 3px 8px rgba(0,0,0,.18);">
        <li>We are entrepreneurs.</li>
        <li>We are committed to get things done.</li>
        <li>We work closely with the client side by side.</li>
        <li>We apply structured methods of reasoning.</li>
        <li>We look at the problem from various angles.</li>
        <li>We are not afraid of delivering unconventional solutions.</li>
        <li>We analyze situations, develop solutions and implement results.</li>
      </ul>
      <svg class="footer-rule" viewBox="0 0 570 24" aria-hidden="true">
        <path d="M0 2 Q270 14 536 20" fill="none" stroke="var(--rule)" stroke-width="2"/>
      </svg>
      <div class="page-number">6</div>
    </section>
  </main>
</body>
</html>
```